Harbor Law Stationary - Law Firm

I am looking for a designer who can help me design letterhead and envelopes consistent with our new business cards. Feel free to reach out to me directly at ned@harborlawgroup.example. Thank you!! Visit harborlawgroup.example to see our site and the attached files for creative assets.

Target Market(s)

Anyone needing a lawyer

Font styles to use
Other font styles liked:
• Adobe Caslon Pro

Requirements
Must have
• Adobe Caslon Pro font
Full color
Nice to have
• My photo on front along with 2/3 face of camo - see mock up for example of what I have in mind.

American colors - similar to the ones found on my website and gold.

```html
<!DOCTYPE html>
<html lang="en">
<head>
<meta charset="utf-8">
<title>Harbor Law Stationery – Envelopes</title>
<link rel="stylesheet" href="https://fonts.googleapis.com/css2?family=Libre+Caslon+Text:wght@400;700&display=swap">
<style>
  :root {
    --backdrop: #ecebea;
    --paper: #ffffff;
    --paper-edge: #dcdcdc;
    --navy: #0e1e3d;
    --gold: #a8955a;
    --ink: #55555a;
    --flap-text: #ffffff;
  }
  * { box-sizing: border-box; margin: 0; padding: 0; }
  html, body {
    width: 1200px; height: 800px; overflow: hidden;
    background: var(--backdrop);
    font-family: "Libre Caslon Text", "Georgia", serif;
  }
  .canvas {
    position: relative; width: 1200px; height: 800px;
  }
  .envelope {
    position: absolute; left: 240px; width: 720px; height: 330px;
    background: var(--paper);
    border: 1px solid var(--paper-edge);
    box-shadow: 0 2px 0 #e3e3e3, 0 4px 0 #ededed;
    overflow: hidden;
  }
  .envelope--back { top: 40px; }
  .envelope--front { top: 420px; }

  .flap {
    position: absolute; left: 0; top: 0; width: 100%; height: 96px;
    background: var(--navy);
    border-radius: 0 0 40px 40px;
    display: flex; align-items: center; justify-content: center;
  }
  .flap__mission {
    color: var(--flap-text);
    font-size: 22px; letter-spacing: 0.3px;
    white-space: nowrap;
  }
  .flap-seam {
    position: absolute; left: 0; top: 96px; width: 100%; height: 234px;
    border-top: 1px solid #f0f0f0;
  }

  .brand {
    position: absolute; left: 56px; top: 72px;
    color: var(--gold);
    font-weight: 700; font-size: 30px; letter-spacing: 3px;
    text-transform: uppercase;
    white-space: nowrap;
  }
  .contact {
    position: absolute; left: 56px; top: 160px;
    color: var(--ink); font-size: 15px; line-height: 1.45;
    list-style: none;
  }
  .contact__line { display: flex; align-items: center; gap: 8px; white-space: nowrap; }
  .contact__icon { width: 14px; height: 14px; flex: none; }
  .contact__icon path, .contact__icon circle, .contact__icon rect { fill: none; stroke: var(--gold); stroke-width: 1.6; }
</style>
</head>
<body>
<main class="canvas">

  <section class="envelope envelope--back" aria-label="Envelope back">
    <div class="flap">
      <p class="flap__mission">Our Mission: To Stand Beside You, Always</p>
    </div>
    <div class="flap-seam"></div>
  </section>

  <section class="envelope envelope--front" aria-label="Envelope front">
    <p class="brand">Harbor Law</p>
    <ul class="contact">
      <li class="contact__line">48 Wharf Lane</li>
      <li class="contact__line">Bayport, FL 30000</li>
      <li class="contact__line">
        <svg class="contact__icon" viewBox="0 0 16 16" aria-hidden="true"><path d="M4 2 L6.5 5 L5 6.5 Q6.5 9.5 9.5 11 L11 9.5 L14 12 L12 14 Q5 13 2 4 Z"/></svg>
        (555) 010-2468
      </li>
      <li class="contact__line">
        <svg class="contact__icon" viewBox="0 0 16 16" aria-hidden="true"><rect x="1.5" y="3.5" width="13" height="9"/><path d="M1.5 3.5 L8 9 L14.5 3.5"/></svg>
        ivy@harborlawgroup.example
      </li>
      <li class="contact__line">
        <svg class="contact__icon" viewBox="0 0 16 16" aria-hidden="true"><circle cx="8" cy="8" r="6.5"/><path d="M1.5 8 H14.5 M8 1.5 Q4 8 8 14.5 M8 1.5 Q12 8 8 14.5"/></svg>
        www.harborlawgroup.example
      </li>
    </ul>
  </section>

</main>
</body>
</html>
```